interior designer/stylist looking for a letter press business card to reflect the stylish work

Hello Designers,
I need a business card design for an company called Mosaic Interior Design. I'm aiming at the high end residential and private client market in London providing sleek simple interiors. I'd like my business card to be pinterest worthy and expensive looking, i want people to pin it and for it to have a sought after look, and want prospective customers to hire me as their interior designer as my card is so beautiful.
I love letter press design. I also like the use of colour/foil on the edge.
Colour combos & general things I like -
Black and White
Navy Blue and Gold
Neutral colours (muted palette of greys whites navys beiges)
White Marble & brass
Vorelle (fashion designer)
....also open to other suggestions....
Please dont take the pink in the attached photos too literally. i'd like the card to look more masculine than feminine.
I'd like Mosaic on one side in one font, with interior design underneath so one word will make the statement....... unless anyone has any other ideas, open to suggestions.
I'd like a really simple font and for the whole card to look very graphic.
my details -
Petra Wendlecombe
Interior Designer & Stylist
email petra@mosaicinteriordesign.co.uk
phone +447311584209
website wwww.mosaicinteriordesign.co.uk
GO GO GO!! EXCITED TO SEE THE OUTCOME!!
x P
Target Market(s)
High End Residential and private clients
Industry/Entity Type
Business
Contact Information for Business Card
Mosaic Interior Design & Styling
Petra Wendlecombe
phone +447311584209

```html
<!DOCTYPE html>
<html lang="en">
<head>
<meta charset="utf-8">
<title>Mosaic Interior Design – Business Card</title>
<link href="https://fonts.googleapis.com/css2?family=Open+Sans:wght@300;400;600;700&display=swap" rel="stylesheet">
<style>
  :root {
    --page: #d6d6d4;
    --card: #f5a623;
    --wordmark: #c27a0e;
    --ink: #ffffff;
    --rule: rgba(255, 255, 255, 0.75);
  }
  * { margin: 0; padding: 0; box-sizing: border-box; }
  html, body {
    width: 1200px;
    height: 900px;
    overflow: hidden;
    background: var(--page);
    font-family: "Open Sans", sans-serif;
  }
  .sheet {
    width: 1200px;
    height: 900px;
    display: flex;
    flex-direction: column;
    align-items: center;
    justify-content: center;
    gap: 40px;
  }
  .card {
    position: relative;
    width: 600px;
    height: 387px;
    background: var(--card);
    border-radius: 4px;
  }
  .wordmark {
    color: var(--wordmark);
    font-weight: 700;
    text-transform: uppercase;
    line-height: 0.95;
    letter-spacing: 0.02em;
    white-space: nowrap;
  }
  .card--front .wordmark {
    position: absolute;
    left: 0;
    right: 0;
    top: 138px;
    text-align: center;
    font-size: 44px;
  }
  .card--back .wordmark {
    position: absolute;
    right: 40px;
    top: 78px;
    text-align: center;
    font-size: 29px;
  }
  .holder {
    position: absolute;
    left: 40px;
    top: 130px;
    color: var(--ink);
    white-space: nowrap;
  }
  .holder__name {
    font-size: 19px;
    font-weight: 600;
    line-height: 1.2;
  }
  .holder__role {
    font-size: 14px;
    font-weight: 300;
    margin-top: 4px;
  }
  .divider {
    position: absolute;
    left: 245px;
    right: 40px;
    top: 188px;
    height: 1px;
    background: var(--rule);
  }
  .contacts {
    position: absolute;
    right: 40px;
    top: 250px;
    list-style: none;
    color: var(--ink);
    font-size: 16px;
    font-weight: 400;
  }
  .contacts__item {
    display: flex;
    align-items: center;
    justify-content: flex-end;
    gap: 12px;
    height: 28px;
    white-space: nowrap;
  }
  .contacts__icon {
    width: 16px;
    height: 16px;
    flex: none;
  }
</style>
</head>
<body>
<main class="sheet">
  <section class="card card--front" aria-label="Business card front">
    <div class="wordmark">Mosaic<br>Interior Design</div>
  </section>

  <section class="card card--back" aria-label="Business card back">
    <div class="holder">
      <p class="holder__name">Petra Wendlecombe</p>
      <p class="holder__role">Interior Designer &amp; Stylist</p>
    </div>
    <div class="wordmark">Mosaic<br>Interior Design</div>
    <div class="divider"></div>
    <ul class="contacts">
      <li class="contacts__item">
        <span>+447311584209</span>
        <svg class="contacts__icon" viewBox="0 0 16 16" aria-hidden="true">
          <path fill="#fff" d="M1 5c0-2 3-3 7-3s7 1 7 3v1h-4V5H5v1H1z"/>
          <rect x="3" y="7" width="10" height="7" rx="1" fill="#fff"/>
          <circle cx="8" cy="10.5" r="1.8" fill="#f5a623"/>
        </svg>
      </li>
      <li class="contacts__item">
        <span>petra@mosaicinteriordesign.co.uk</span>
        <svg class="contacts__icon" viewBox="0 0 16 16" aria-hidden="true">
          <rect x="1" y="3" width="14" height="10" rx="1" fill="#fff"/>
          <path d="M1.5 4 8 9l6.5-5" fill="none" stroke="#f5a623" stroke-width="1.3"/>
        </svg>
      </li>
      <li class="contacts__item">
        <span>www.mosaicinteriordesign.co.uk</span>
        <svg class="contacts__icon" viewBox="0 0 16 16" aria-hidden="true">
          <g fill="none" stroke="#fff" stroke-width="1.8" stroke-linecap="round">
            <path d="M7 9 9 7"/>
            <path d="M6 7.5 4 9.5a2.1 2.1 0 0 0 3 3l2-2"/>
            <path d="M10 8.5l2-2a2.1 2.1 0 0 0-3-3l-2 2"/>
          </g>
        </svg>
      </li>
    </ul>
  </section>
</main>
</body>
</html>
```